Business card for medical clinic

I need an upmarket, modern medical/health business card for my clinic

Contact Information for Business Card

name, address, email, qr code

```html
<!DOCTYPE html>
<html lang="en">
<head>
<meta charset="utf-8">
<title>Alder Ridge Clinic – Business Card</title>
<link rel="stylesheet" href="https://fonts.googleapis.com/css2?family=Cinzel:wght@500&family=Noto+Serif:wght@400&display=swap">
<style>
  :root {
    --page-bg: #d3d4d6;
    --navy: #2a2f45;
    --steel: #3f6f91;
    --sky: #38b0df;
    --white: #ffffff;
    --ink: #2b2b2b;
    --accent: #1f5f8f;
    --icon: #2a7fc0;
  }
  * { margin: 0; padding: 0; box-sizing: border-box; }
  html, body { width: 900px; height: 1200px; overflow: hidden; }
  body { background: var(--page-bg); position: relative; font-family: "Noto Serif", Georgia, serif; }

  .card { position: absolute; width: 632px; height: 364px; overflow: hidden; }

  .card-front {
    left: 133px; top: 210px;
    background: linear-gradient(90deg, var(--navy) 0%, var(--steel) 55%, var(--sky) 100%);
    display: flex; align-items: center; justify-content: center;
  }
  .brand-name {
    font-family: "Noto Serif", Georgia, serif; font-weight: 400;
    font-size: 30px; color: var(--white);
  }

  .card-back { left: 134px; top: 624px; background: var(--white); }
  .details { position: absolute; left: 202px; top: 90px; color: var(--ink); font-size: 15px; }
  .person-name {
    font-family: "Cinzel", "Times New Roman", serif; font-weight: 500;
    font-size: 22px; letter-spacing: 0.5px; color: var(--accent); line-height: 28px;
  }
  .person-role { line-height: 20px; }
  .address { margin-top: 13px; line-height: 22px; }
  .contact { margin-top: 14px; list-style: none; line-height: 25px; }
  .contact li { display: flex; align-items: center; gap: 6px; }
  .contact svg { width: 12px; height: 12px; fill: var(--icon); flex: none; }
  .phone { letter-spacing: 2px; }
</style>
</head>
<body>
  <section class="card card-front">
    <span class="brand-name">Alder Ridge Clinic</span>
  </section>

  <section class="card card-back">
    <div class="details">
      <h1 class="person-name">DANIEL WHITMORE</h1>
      <p class="person-role">Principal Consultant</p>
      <p class="address">PO Box 418205<br>Willow Creek, Alaska 99688</p>
      <ul class="contact">
        <li class="phone">
          <svg viewBox="0 0 24 24" aria-hidden="true"><path d="M6.6 10.8a15.1 15.1 0 0 0 6.6 6.6l2.2-2.2c.3-.3.7-.4 1-.2 1.1.4 2.3.6 3.6.6.6 0 1 .4 1 1V20c0 .6-.4 1-1 1A17 17 0 0 1 3 4c0-.6.4-1 1-1h3.5c.6 0 1 .4 1 1 0 1.3.2 2.5.6 3.6.1.3 0 .7-.2 1z"/></svg>
          +1-907-555-0142
        </li>
        <li>
          <svg viewBox="0 0 24 24" aria-hidden="true"><path d="M2 5h20v14H2z M2 5l10 8 10-8" /></svg>
          info@alderridgeclinicgroup.com
        </li>
        <li>
          <svg viewBox="0 0 24 24" aria-hidden="true"><path d="M12 2a10 10 0 1 0 0 20 10 10 0 0 0 0-20zm0 2c.9 1.2 1.6 2.6 2 4h-4c.4-1.4 1.1-2.8 2-4zM4.3 14a8 8 0 0 1 0-4h3.4a16 16 0 0 0 0 4zm.8 2h3c.3 1.2.8 2.4 1.4 3.5A8 8 0 0 1 5.1 16zm3-8h-3a8 8 0 0 1 4.4-3.5C8.9 5.6 8.4 6.8 8.1 8zM12 20c-.9-1.2-1.6-2.6-2-4h4c-.4 1.4-1.1 2.8-2 4zm2.3-6H9.7a14 14 0 0 1 0-4h4.6a14 14 0 0 1 0 4zm.2 5.5c.6-1.1 1.1-2.3 1.4-3.5h3a8 8 0 0 1-4.4 3.5zm1.8-5.5a16 16 0 0 0 0-4h3.4a8 8 0 0 1 0 4zm-.4-6c-.3-1.2-.8-2.4-1.4-3.5A8 8 0 0 1 18.9 8z"/></svg>
          www.alderridgeclinicgroup.com
        </li>
      </ul>
    </div>
  </section>
</body>
</html>
```